Bramblewood Card Company Business Cards

We are a trading card store with Glimmorax, sports and other TCG cards, we need a business card design that encompasses a clean cut, modern style with a retro flare. website is bramblewoodcardco.com for reference. Can utilize a comic book era feel or a more modern outdoor feel to utilize the "Pacific Northwest" elements of tress, mountains, etc.

Industry/Entity Type

Trading cards and collectibles

Contact Information for Business Card

business name, email address, phone number, name, owner job title

Font styles to use
Sans Serif

```html
<!DOCTYPE html>
<html lang="en">
<head>
<meta charset="utf-8">
<title>Bramblewood Card Company – Business Cards</title>
<link href="https://fonts.googleapis.com/css2?family=Arimo:wght@400;700&display=swap" rel="stylesheet">
<style>
  :root {
    --backdrop: #2e2e2e;
    --card-grey: #6e6e6e;
    --card-white: #ffffff;
    --ink-grey: #5a5a5a;
    --ink-dark: #3a3a3a;
    --accent-blue: #1eb4dc;
    --divider: #d6d6d6;
  }
  * { margin: 0; padding: 0; box-sizing: border-box; }
  html, body {
    width: 1200px;
    height: 689px;
    overflow: hidden;
    background: var(--backdrop);
    font-family: "Arimo", Arial, sans-serif;
  }
  .canvas {
    position: relative;
    width: 1200px;
    height: 689px;
  }
  .card {
    position: absolute;
    top: 196px;
    width: 520px;
    height: 298px;
    border-radius: 18px;
    overflow: hidden;
  }

  /* Card back */
  .card-back {
    left: 50px;
    background: var(--card-grey);
    display: flex;
    align-items: center;
    justify-content: center;
  }
  .brand-mark {
    display: flex;
    align-items: center;
    gap: 12px;
  }
  .brand-mark__dot {
    width: 18px;
    height: 18px;
    border-radius: 50%;
    background: var(--accent-blue);
    flex: none;
  }
  .brand-mark__name {
    font-weight: 700;
    font-size: 24px;
    line-height: 1.15;
    letter-spacing: 0.5px;
    text-transform: uppercase;
  }
  .card-back .brand-mark__name { color: var(--card-white); }

  /* Card front */
  .card-front {
    left: 630px;
    background: var(--card-white);
  }
  .card-front .brand-block {
    position: absolute;
    left: 28px;
    top: 0;
    width: 220px;
    height: 250px;
    display: flex;
    align-items: center;
  }
  .card-front .brand-mark__name {
    color: var(--ink-grey);
    font-size: 20px;
  }
  .front-divider {
    position: absolute;
    left: 262px;
    top: 60px;
    width: 1px;
    height: 118px;
    background: var(--divider);
  }
  .contact-block {
    position: absolute;
    left: 282px;
    top: 62px;
  }
  .person-name {
    color: var(--accent-blue);
    font-weight: 700;
    font-size: 24px;
    line-height: 1.1;
  }
  .person-title {
    color: var(--ink-grey);
    font-size: 13px;
    margin-top: 2px;
  }
  .contact-list {
    list-style: none;
    margin-top: 18px;
  }
  .contact-list li {
    display: flex;
    align-items: center;
    gap: 8px;
    color: var(--ink-dark);
    font-size: 13px;
    line-height: 19px;
  }
  .contact-list svg {
    width: 11px;
    height: 11px;
    flex: none;
    fill: var(--accent-blue);
  }
  .accent-rule {
    position: absolute;
    left: 0;
    right: 0;
    bottom: 22px;
    height: 2px;
    background: var(--accent-blue);
  }
</style>
</head>
<body>
<main class="canvas">

  <section class="card card-back" aria-label="Card back">
    <div class="brand-mark">
      <span class="brand-mark__dot"></span>
      <span class="brand-mark__name">Bramblewood<br>Card Company</span>
    </div>
  </section>

  <section class="card card-front" aria-label="Card front">
    <div class="brand-block">
      <div class="brand-mark">
        <span class="brand-mark__dot"></span>
        <span class="brand-mark__name">Bramblewood<br>Card Company</span>
      </div>
    </div>

    <div class="front-divider"></div>

    <div class="contact-block">
      <p class="person-name">Jared Holloway</p>
      <p class="person-title">President</p>
      <ul class="contact-list">
        <li>
          <svg viewBox="0 0 24 24" aria-hidden="true"><path d="M6.6 10.8a15 15 0 0 0 6.6 6.6l2.2-2.2c.3-.3.7-.4 1-.2 1.1.4 2.3.6 3.6.6.6 0 1 .4 1 1V20c0 .6-.4 1-1 1A17 17 0 0 1 3 4c0-.6.4-1 1-1h3.5c.6 0 1 .4 1 1 0 1.3.2 2.5.6 3.6.1.3 0 .7-.2 1z"/></svg>
          <span>555-014-2297</span>
        </li>
        <li>
          <svg viewBox="0 0 24 24" aria-hidden="true"><path d="M2 5h20v14H2z M3.5 6.5 12 13l8.5-6.5" fill="none" stroke="#1eb4dc" stroke-width="2.4"/></svg>
          <span>info@bramblewoodcardco.com</span>
        </li>
        <li>
          <svg viewBox="0 0 24 24" aria-hidden="true"><circle cx="12" cy="12" r="10"/><path d="M2 12h20M12 2c3 3 3 17 0 20M12 2c-3 3-3 17 0 20" fill="none" stroke="#ffffff" stroke-width="1.4"/></svg>
          <span>www.bramblewoodcardco.com</span>
        </li>
      </ul>
    </div>

    <div class="accent-rule"></div>
  </section>

</main>
</body>
</html>
```